Upmarket Dessert Lounge needs a Business Card Design

We are an upmarket dessert lounge needing a business card to match our image.

We want something that is simple yet beautiful, feminine, classy, sophisticated and elegant. We want it to stand out and don't mind if it is bold.

The design should include our logo and colours of red or maroon with gold highlights. We don't mind if black is used.

Marlow & Quince

Target Market(s)

For those who like to indulge or treat themselves and give in to their temptations on good quality desserts.

Industry/Entity Type

Business

Requirements
Must have
• Must include our logo and our name

Marlow & Quince

M & Q

```html
<!DOCTYPE html>
<html lang="en">
<head>
<meta charset="utf-8">
<title>Marlow &amp; Quince — Business Card</title>
<link rel="stylesheet" href="https://fonts.googleapis.com/css2?family=Open+Sans:wght@400;600;700&display=swap">
<style>
  :root {
    --maroon: #7a1315;
    --cream: #f9d7a0;
    --paper: #ffffff;
    --ink: #3a3a3a;
    --backdrop: #e6e6e6;
  }
  html, body {
    margin: 0;
    padding: 0;
    width: 956px;
    height: 1200px;
    overflow: hidden;
    background: var(--backdrop);
    font-family: "Open Sans", Arial, sans-serif;
  }
  .canvas {
    position: relative;
    width: 956px;
    height: 1200px;
  }
  .card {
    position: absolute;
    width: 797px;
    height: 454px;
    border-radius: 28px;
    overflow: hidden;
  }
  .card--front {
    left: 69px;
    top: 97px;
    background: var(--paper);
  }
  .card--back {
    left: 74px;
    top: 632px;
    background: var(--maroon);
  }
  .front-swoosh {
    position: absolute;
    left: 0;
    top: 0;
    width: 797px;
    height: 454px;
  }
  .brand-name {
    position: absolute;
    left: 0;
    right: 0;
    top: 86px;
    text-align: center;
    font-size: 40px;
    font-weight: 600;
    letter-spacing: 1px;
    color: var(--maroon);
  }
  .person {
    position: absolute;
    left: 0;
    right: 0;
    top: 233px;
    text-align: center;
    font-size: 23px;
    color: var(--ink);
  }
  .person__name { font-weight: 700; }
  .contact {
    position: absolute;
    left: 0;
    right: 0;
    top: 288px;
    text-align: center;
    font-size: 17px;
    line-height: 28px;
    color: var(--ink);
  }
  .contact b { font-weight: 700; }
  .address {
    position: absolute;
    left: 398px;
    width: 290px;
    top: 386px;
    text-align: center;
    font-size: 18px;
    line-height: 27px;
    color: var(--paper);
  }
  .monogram {
    position: absolute;
    left: 0;
    right: 0;
    top: 0;
    bottom: 0;
    display: flex;
    align-items: center;
    justify-content: center;
    font-size: 96px;
    font-weight: 600;
    color: var(--cream);
    letter-spacing: 2px;
  }
</style>
</head>
<body>
<main class="canvas">
  <section class="card card--front">
    <svg class="front-swoosh" viewBox="0 0 797 454" aria-hidden="true">
      <path d="M0,398 C150,380 300,365 420,356 C300,370 150,405 0,440 Z" fill="var(--cream)"/>
      <path d="M0,452 C150,405 350,362 480,356 C620,352 740,375 797,403 L797,454 L0,454 Z" fill="var(--maroon)"/>
    </svg>
    <div class="brand-name">Marlow &amp; Quince</div>
    <div class="person"><span class="person__name">Your Name -</span> Designation</div>
    <div class="contact">
      <div><b>p</b> : 123-456-7890 &nbsp;|&nbsp; <b>c</b> : 123-456-7890 &nbsp;|&nbsp; <b>f</b> : 123-456-7890</div>
      <div><b>e</b> : name@yourwebsite.com &nbsp;|&nbsp; <b>w</b> : www.marlowquince.com</div>
    </div>
    <div class="address">
      <div>0000, Street Name</div>
      <div>City Name, Country Code.</div>
    </div>
  </section>

  <section class="card card--back">
    <div class="monogram">M &amp; Q</div>
  </section>
</main>
</body>
</html>
```